A fantastic website for a physio

We are looking for an eye catching website which can attract as many customer as possible.
We have logo designed and ready to be used in the website.
Please use the green and blue which is used in our logo for the preferred colors.
The following are the designs that I Iike:
http://www.example-clinicone.com.au/
http://www.example-rehabtwo.com.au/
We will be having other services including massage therapy, Psychology and podiatrist. You can find information about podiatry in our condition sheet.
for the address you can put Shop 5/248 Wattlebrook Street, Kelvindale. It might change but for now you can leave it until I confirm that in the next couple of days.

Logo file can be downloaded here:
https://files.example-share.net/s/qz4mtl9wkr82bvx/Logo1511.jpg?dl=0

Target Market(s)

Infant to old people.
We speak Farsi.

Industry/Entity Type

Physical Therapy

Number of Pages Required

5+ page

Font styles to use
Serif

Colors
33a6d7
abd037
e667a6

Requirements
Must have
• Home, About , our services, Conditions we treat and contact
• For home page and contacts we would like a tab that can connect to another website(bookwell) for online booking. We would like the patient's to be able to leave us massage or leave their email for monthly news letter. For the condition we treat you can use the condition sheets I have attached. For about us and home page you can use brochure I have attached.
• The other things should have include: in-line contact form, Google Map, clinic hours, newsletter sign-up etc, schema rich contact information
• Social media connection to our Facebook, Instagram and linked in
Nice to have
• Search engine optimization for Merrylands and Parramatta physiotherapy.
• We can speak English and Farsi. So is nice to have an information tab for Farsi speaking people. I can provide you with the texts.

```html
<!DOCTYPE html>
<html lang="en">
<head>
<meta charset="utf-8">
<title>Our Services</title>
<link rel="stylesheet" href="https://fonts.googleapis.com/css2?family=Arimo:ital,wght@0,400;0,700;1,400&display=swap">
<style>
  :root {
    --blue: #3aa8dc;
    --nav-blue: #45b0df;
    --green: #abd037;
    --pink: #e667a6;
    --ink: #222;
    --active: #3b4246;
    --rule: #e6e6e6;
    --band: #f4f4f4;
  }
  * { box-sizing: border-box; margin: 0; padding: 0; }
  html, body { width: 1200px; height: 1180px; overflow: hidden; background: #fff; }
  body { position: relative; font-family: "Arimo", Arial, sans-serif; color: var(--ink); }

  .site-nav { position: absolute; top: 0; left: 0; width: 1200px; height: 45px; background: var(--nav-blue); }
  .tagline { position: absolute; top: 1px; left: 150px; font-size: 13px; color: rgba(90,110,120,.75); z-index: 1; }
  .nav-item { position: absolute; top: 0; height: 45px; line-height: 42px; font-size: 11px; font-weight: 700; letter-spacing: 3.2px; color: #fff; text-transform: uppercase; z-index: 2; }
  .nav-item.active { background: var(--active); color: var(--green); padding: 0 14px; }
  .nav-item .caret { display: inline-block; margin-left: 6px; border: 4px solid transparent; border-top-color: #fff; vertical-align: -1px; }
  .search-icon { position: absolute; top: 13px; left: 692px; z-index: 2; }

  .section-title { position: absolute; left: 150px; width: 898px; text-align: center; color: var(--blue); font-weight: 700; font-size: 37px; }
  .rule { position: absolute; left: 150px; width: 898px; height: 1px; background: var(--rule); }
  .kicker { position: absolute; top: 164px; left: 150px; width: 898px; text-align: center; font-style: italic; font-size: 14px; color: var(--blue); }
  .intro { position: absolute; top: 192px; left: 160px; width: 878px; text-align: center; font-size: 13.5px; line-height: 19.5px; }

  .service { position: absolute; width: 280px; }
  .service-photo { width: 251px; height: 177px; border-radius: 4px; }
  .service h2 { margin-top: 17px; font-size: 24px; font-weight: 700; color: var(--blue); letter-spacing: -.2px; }
  .service p { margin-top: 7px; font-size: 13.6px; line-height: 19.4px; }
  .service p .line { display: block; text-align: justify; text-align-last: justify; white-space: nowrap; }
  .btn-more { display: block; margin-top: 15px; width: 126px; height: 44px; line-height: 44px; padding-left: 35px; background: var(--pink); color: #fff; font-size: 17px; font-weight: 700; letter-spacing: -.3px; }

  .contact-band { position: absolute; top: 1040px; left: 150px; width: 898px; height: 140px; background: var(--band); }
  .contact-note { position: absolute; top: 1157px; left: 164px; font-size: 14px; }
  .field { position: absolute; top: 1154px; width: 232px; height: 40px; border: 1px solid #ccc; border-radius: 3px; background: #fff; padding: 8px 12px; font-size: 14px; color: #666; }
</style>
</head>
<body>
  <nav class="site-nav">
    <span class="tagline">your body deserves the best of care.</span>
    <span class="nav-item" style="left:36px">Home</span>
    <span class="nav-item" style="left:112px">About</span>
    <span class="nav-item active" style="left:183px;width:151px">Our Services</span>
    <span class="nav-item" style="left:349px">Contact</span>
    <span class="nav-item" style="left:454px">Conditions We Treat<span class="caret"></span></span>
    <svg class="search-icon" width="12" height="12" viewBox="0 0 12 12" aria-label="Search"><circle cx="5" cy="5" r="3.6" fill="none" stroke="#fff" stroke-width="1.8"/><line x1="7.6" y1="7.6" x2="11" y2="11" stroke="#fff" stroke-width="2"/></svg>
    <span class="nav-item" style="left:1038px">English</span>
    <span class="nav-item" style="left:1140px">Farsi</span>
  </nav>

  <h1 class="section-title" style="top:84px">OUR SERVICES</h1>
  <div class="rule" style="top:142px"></div>
  <div class="kicker">HARBOURLINE PHYSIOTHERAPY</div>
  <p class="intro">We care that you feel better. We consider every person who actively involves themselves in the treatment process at our clinic to be a part of our wider “family community”</p>

  <article class="service" style="left:150px;top:259px">
    <div class="service-photo" role="img" aria-label="Physiotherapist treating a patient's leg" style="background:linear-gradient(135deg,#e9eef2,#c9d3db 60%,#5a6f8c)"></div>
    <h2>Physiotherapy</h2>
    <p><span class="line">Lorem Ipsum is simply dummy text of the</span><span class="line">printing and typesetting industry. Lorem</span><span class="line">Ipsum has been the industry's standard</span><span class="line">dummy text ever since the 1500s...</span></p>
    <span class="btn-more">More...</span>
  </article>
  <article class="service" style="left:458px;top:259px">
    <div class="service-photo" role="img" aria-label="Shock wave device applied to a patient's shoulder" style="background:linear-gradient(90deg,#3f6f9c,#c9ced3 45%,#f2f2f2)"></div>
    <h2>Shock Wave Therapy</h2>
    <p><span class="line">Lorem Ipsum is simply dummy text of the</span><span class="line">printing and typesetting industry. Lorem</span><span class="line">Ipsum has been the industry's standard</span><span class="line">dummy text ever since the 1500s...</span></p>
    <span class="btn-more">More...</span>
  </article>
  <article class="service" style="left:767px;top:259px">
    <div class="service-photo" role="img" aria-label="Therapist examining an injured ankle" style="background:linear-gradient(160deg,#eef0ef,#d8b9a4 45%,#2c8fbf)"></div>
    <h2>Sports Injuries</h2>
    <p><span class="line">Lorem Ipsum is simply dummy text of the</span><span class="line">printing and typesetting industry. Lorem</span><span class="line">Ipsum has been the industry's standard</span><span class="line">dummy text ever since the 1500s...</span></p>
    <span class="btn-more">More...</span>
  </article>

  <article class="service" style="left:150px;top:649px">
    <div class="service-photo" role="img" aria-label="Dry needling treatment on a back" style="background:linear-gradient(135deg,#d9dde2,#e8cdbb 55%,#d4b09a)"></div>
    <h2>Dry Needling</h2>
    <p><span class="line">Lorem Ipsum is simply dummy text of the</span><span class="line">printing and typesetting industry. Lorem</span><span class="line">Ipsum has been the industry's standard</span><span class="line">dummy text ever since the 1500s...</span></p>
    <span class="btn-more">More...</span>
  </article>
  <article class="service" style="left:458px;top:649px">
    <div class="service-photo" role="img" aria-label="Woman sitting on grass outdoors" style="background:linear-gradient(180deg,#eef3e4,#a9c27a 55%,#5f8a3a)"></div>
    <h2>Women’s Health</h2>
    <p><span class="line">Lorem Ipsum is simply dummy text of the</span><span class="line">printing and typesetting industry. Lorem</span><span class="line">Ipsum has been the industry's standard</span><span class="line">dummy text ever since the 1500s...</span></p>
    <span class="btn-more">More...</span>
  </article>
  <article class="service" style="left:767px;top:649px">
    <div class="service-photo" role="img" aria-label="Bandaged hand filling in a work injury form" style="background:linear-gradient(135deg,#5c5f63,#e6e6e6 35%,#f2ece6 70%,#d7a98f)"></div>
    <h2>Work Cover Claims</h2>
    <p><span class="line">Lorem Ipsum is simply dummy text of the</span><span class="line">printing and typesetting industry. Lorem</span><span class="line">Ipsum has been the industry's standard</span><span class="line">dummy text ever since the 1500s...</span></p>
    <span class="btn-more">More...</span>
  </article>

  <section class="contact-band"></section>
  <h2 class="section-title" style="top:1077px">CONTACT</h2>
  <div class="rule" style="top:1134px;left:164px;width:870px;background:#e2e2e2"></div>
  <p class="contact-note">Contact us and we'll get back to you within 24 hours.</p>
  <div class="field" style="left:538px">Name</div>
  <div class="field" style="left:800px">Email</div>
</body>
</html>
```